The design should look similar to the uploaded example to accommodate the information needed for a business card template. I would like to see the colors orange and charcoal grey incorporated along with the logo.The following should be on the back of the card SPECIALIZING IN NEW AND USED TIRES & WHEELS FOR:- Loaders- Skid Steers- Telehandlers- Boom Lifts- Forklifs and moreELIMINATING DOWNTIMEWheel Exchange Program for New & Used Foam Filled and Solid Rubber TiresSPECIALTY SERVICES- Foam Filling Tires- Largest Tire Press in SE- ONSITE Forklift Tire Press- Boom Truck Services - Rubber Tracks

Target Market(s)

New and Existing Customers

Industry/Entity Type

Business

Contact Information for Business Card

NAMEHEAVY DUTY TIRE, LLC8470 Belvedere RoadWest Palm Beach, FL 33411P: 844-HD-TIRESF: 561-431-6469C:E: W: WWW.GRANITERIMSUPPLY-EXAMPLE.COM

Font styles to use
Sans Serif

Colors
f37122
333333

Requirements
Must have
• The logo and the information indicated for the backside of the card
Nice to have
• Keep the orange and charcoal grey colors

```html
<!DOCTYPE html>
<html lang="en">
<head>
<meta charset="utf-8">
<title>Granite Rim Supply — Business Card</title>
<link href="https://fonts.googleapis.com/css2?family=Open+Sans:wght@400;600;700&display=swap" rel="stylesheet">
<style>
  :root {
    --orange: #f37122;
    --charcoal: #333333;
    --slate: #2f3a3d;
    --white: #ffffff;
    --backdrop: #e9e6e1;
    --text-dark: #2b2b2b;
  }
  * { box-sizing: border-box; margin: 0; padding: 0; }
  html, body {
    width: 1200px; height: 900px; overflow: hidden;
    background: var(--backdrop);
    font-family: "Open Sans", Arial, sans-serif;
  }
  .canvas { position: relative; width: 1200px; height: 900px; }
  .card {
    position: absolute; left: 250px; width: 700px; height: 400px;
    overflow: hidden;
    box-shadow: 0 6px 18px rgba(0,0,0,0.18);
  }
  /* Back side */
  .card-back {
    top: 30px;
    background: var(--charcoal);
    color: var(--white);
    text-align: center;
    padding: 40px 40px;
    display: flex; flex-direction: column; justify-content: center; gap: 6px;
  }
  .back-heading {
    color: var(--orange); font-weight: 600; text-transform: uppercase;
    font-size: 19px; letter-spacing: 0.5px;
  }
  .back-heading.large { font-size: 23px; margin-top: 6px; }
  .back-heading.mid { margin-top: 6px; }
  .back-line { font-size: 17px; line-height: 1.35; }
  .dot {
    display: inline-block; width: 8px; height: 8px; border-radius: 50%;
    background: var(--orange); margin: 0 12px; vertical-align: middle;
  }
  /* Front side */
  .card-front { top: 470px; background: var(--white); }
  .corner-mark { position: absolute; left: 0; top: 38px; }
  .person-name {
    position: absolute; left: 86px; top: 44px;
    color: var(--orange); font-weight: 600; font-size: 24px;
  }
  .details { position: absolute; left: 40px; top: 100px; }
  .company-name {
    color: var(--orange); font-size: 19px; font-weight: 400; margin-bottom: 4px;
  }
  .address { color: var(--text-dark); font-size: 16px; line-height: 1.3; margin-bottom: 6px; }
  .contact-list { list-style: none; }
  .contact-list li {
    color: var(--text-dark); font-size: 16px; line-height: 1.45;
    display: flex; align-items: center; gap: 10px;
  }
  .contact-list svg { width: 13px; height: 13px; flex: none; }
  .brand {
    position: absolute; left: 430px; top: 140px; width: 240px;
    display: flex; align-items: center; gap: 14px;
  }
  .brand-circle {
    width: 64px; height: 64px; border-radius: 50%; background: var(--orange); flex: none;
  }
  .brand-name {
    color: var(--slate); font-weight: 700; font-size: 30px; line-height: 1.05;
  }
  .bottom-bands { position: absolute; left: 0; bottom: 0; }
</style>
</head>
<body>
<main class="canvas">

  <section class="card card-back" aria-label="Business card back">
    <h2 class="back-heading">Specializing in new and used tires &amp; wheels for</h2>
    <p class="back-line">Loaders<span class="dot"></span>Skid Steers<span class="dot"></span>Telehandlers<span class="dot"></span>Boom Lifts</p>
    <p class="back-line">Forklifs and more</p>
    <h2 class="back-heading mid">Eliminating Downtime</h2>
    <p class="back-line">Wheel Exchange Program for New &amp; Used Foam<br>Filled and Solid Rubber Tires</p>
    <h2 class="back-heading large">Specialty Services</h2>
    <p class="back-line">Foam Filling Tires<span class="dot"></span>Largest Tire Press in SE</p>
    <p class="back-line">ONSITE Forklift Tire Press<span class="dot"></span>Boom Truck Services<span class="dot"></span>Rubber Tracks</p>
  </section>

  <section class="card card-front" aria-label="Business card front">
    <svg class="corner-mark" width="70" height="40" viewBox="0 0 70 40">
      <rect x="0" y="0" width="40" height="40" fill="var(--orange)"/>
      <polygon points="38,40 58,0 70,0 70,40" fill="var(--slate)"/>
    </svg>
    <h1 class="person-name">Marcus Delaney</h1>

    <div class="details">
      <p class="company-name">GRANITE RIM SUPPLY, LLC</p>
      <p class="address">5126 Marston Lane<br>Palm Crest, FL 33490</p>
      <ul class="contact-list">
        <li><svg viewBox="0 0 16 16"><path d="M3 1l3 3-2 2a9 9 0 0 0 6 6l2-2 3 3-2 2C7 15 1 9 1 3z" fill="var(--orange)"/></svg>844-GR-WHEEL</li>
        <li><svg viewBox="0 0 16 16"><rect x="1" y="6" width="14" height="9" rx="1" fill="var(--orange)"/><rect x="4" y="1" width="8" height="5" fill="var(--orange)"/></svg>561-278-9053</li>
        <li><svg viewBox="0 0 16 16"><rect x="3" y="1" width="10" height="14" rx="2" fill="none" stroke="var(--orange)" stroke-width="2"/></svg>561-390-2714</li>
        <li><svg viewBox="0 0 16 16"><rect x="1" y="3" width="14" height="10" fill="var(--orange)"/><path d="M1 3l7 6 7-6" fill="none" stroke="#fff" stroke-width="1.4"/></svg>info@graniterimsupply-example.com</li>
        <li><svg viewBox="0 0 16 16"><circle cx="8" cy="8" r="7" fill="var(--orange)"/><path d="M1 8h14M8 1c-3 4-3 10 0 14M8 1c3 4 3 10 0 14" fill="none" stroke="#fff" stroke-width="1"/></svg>www.graniterimsupply-example.com</li>
      </ul>
    </div>

    <div class="brand">
      <span class="brand-circle"></span>
      <span class="brand-name">GRANITE<br>RIM</span>
    </div>

    <svg class="bottom-bands" width="700" height="80" viewBox="0 0 700 80">
      <polygon points="0,0 300,0 282,22 0,22" fill="var(--orange)"/>
      <polygon points="300,22 700,22 700,80 262,80" fill="var(--slate)"/>
    </svg>
  </section>

</main>
</body>
</html>
```